Luxury Tours Design

We are “Amber Coachline” a Chauffeur Company based in Maidenhead, Berkshire. Our website is - ambercoachline.co.uk which will give you an insite into the Company.
Our clients consist of luxurious Hotels, large Corporate Companies along with private UHNW clients.
We have a fleet of Valtrane E, S and V Class vehicles along with 16 Seater Executive Coaches so we can accommodate single travellers, couples, friends, families and groups.
We would like an A5 (or slightly larger) double sided colour leaflet designed to promote our Tours in our local and surrounding areas.
The information below is some indication as to what we would like.
On the front we would like:-
Amber Coachline “Signature Tour” This will be our main promoting Tour
Slogan “Amber Coachline….ever at your service”
Tour will include:-
Visiting the historic town of Windsor, Hollenby Castle, St Aldric’s Chapel and Regal Pemberly Shopping Arcade.
Then onto Eton (Dunmere College) and a lovely view of the River Thames along with an array of Antique Shops in the quaint streets.
Bray Village (Heron Isle), renowed for it’s Brevard Star Restaurants and pubs.
Through picturesque Cookham along to Marlow for some shopping in the boutique shops, small listed buildings and beautiful places for refreshments, along with stunning views of the River Thames form Ashcombe Bridge.
This will be our main tour we offer but again this is flexible. This aims to be around 4-5 hours.
On the front, a picture of Hollenby castle maybe a large picture with writing over the top, or a separate photo….. a couple of photos attached or something similar.
On the back of the leaflet:-
We offer London based tours including:-
Belvards, Larkmoor Park, Ravensholt Palace, Corringdale Palace, Pellington Square, Turning of the Sentries, Keep of Ardmoor, Tall Tom, Glenmoreton Abbey to name a few! Or maybe London by night with a show or restaurant.
On the back a picture of Corringdale Palace…a couple of picture are also attached or again something similar.
Other Tours provided:-
Ridgewell Court Palace, Oxford and Corvane Palace, Ashmarrow Ring and Bath, The Cotswolds, Stratford and Penlow Castle, Quillford Shopping Village.
Also bespoke Tours can be arranged. We can personalise any tour to your requirements.
Experienced friendly Chauffeur’s, no request too big or small.
Please call us on 01632 960417 or email us sales@ambercoachline.co.uk
Please can you do an initial design including the above information.
Look forward to hearing from you.
Kind regards
Please visit https://www.hartleyprivatedrives.co.uk/ to get an idea of the tours of London to go on the back.
Prices will follow to be added after design and layout has been done.
Our AC logo is available on www.ambercoachline.co.uk
We want text to be editable and also for the design to have a luxury feel.
Chauffeur

```html
<!DOCTYPE html>
<html lang="en">
<head>
<meta charset="utf-8">
<title>Amber Coachline – Tours Leaflet</title>
<link rel="stylesheet" href="https://fonts.googleapis.com/css2?family=Great+Vibes&family=Poppins:ital,wght@0,300;0,400;0,500;0,600;1,400;1,600&display=swap">
<style>
  :root {
    --board: #b3b3b3;
    --ink-dark: #2a2924;
    --panel: rgba(120, 106, 62, 0.62);
    --gold: #d2b94e;
    --gold-deep: #a38e3c;
    --script-brown: #4f4630;
    --text-light: #ffffff;
    --text-dark: #2a2620;
    --sky-top: #a9c6dd;
    --sky-pink: #f0a99a;
    --foliage: #3f6b25;
  }
  * { box-sizing: border-box; margin: 0; padding: 0; }
  html, body { width: 1200px; height: 2400px; overflow: hidden; }
  body { background: var(--board); font-family: "Poppins", sans-serif; position: relative; }

  .page {
    position: absolute; left: 230px; width: 740px; height: 1049px;
    background: var(--ink-dark); overflow: hidden;
    box-shadow: 0 14px 34px rgba(0,0,0,0.35);
  }
  .page--front { top: 103px; }
  .page--back { top: 1238px; }

  .abs { position: absolute; }
  .center { left: 0; right: 0; text-align: center; }

  .script-title {
    font-family: "Great Vibes", cursive; color: var(--script-brown);
    font-size: 92px; line-height: 1;
  }
  .slogan { font-family: "Great Vibes", cursive; color: var(--script-brown); font-size: 44px; line-height: 1; }

  /* front photo */
  .castle-photo {
    left: 0; top: 0; width: 740px; height: 560px;
    background:
      linear-gradient(to bottom, rgba(42,41,36,0) 78%, var(--ink-dark) 100%),
      linear-gradient(to bottom, var(--sky-top) 0%, #d8cfd6 22%, var(--sky-pink) 36%, #c9b7a2 44%, #6d7d52 54%, var(--foliage) 72%, #2f4a1d 100%);
  }
  .fleet-intro {
    top: 470px; left: 60px; right: 60px; text-align: center;
    color: var(--text-light); font-size: 18px; line-height: 21px; font-weight: 500;
  }

  .tour-panel { left: 88px; top: 578px; width: 565px; height: 321px; background: var(--panel); }
  .tour-heading {
    left: 21px; top: 9px; color: var(--gold); font-size: 24px; line-height: 25px; font-weight: 500;
  }
  .price-tag {
    left: 380px; top: 6px; width: 185px; height: 50px; background: var(--gold-deep);
    color: var(--text-light); text-align: center; padding-top: 2px;
  }
  .price-tag .amount { font-size: 29px; font-weight: 600; line-height: 30px; }
  .price-tag sup { font-size: 14px; vertical-align: 12px; font-weight: 500; }
  .price-tag .note { font-size: 11.5px; line-height: 13px; }
  .tour-stops { left: 22px; top: 80px; width: 520px; color: var(--text-light); font-size: 12.6px; line-height: 15px; }
  .tour-stops p { margin-bottom: 15px; }
  .quote {
    color: var(--gold); font-style: italic; font-size: 16px; text-align: center;
  }
  .quote .mark { font-family: Georgia, serif; font-style: normal; font-weight: 700; font-size: 28px; line-height: 0; position: relative; top: 4px; }

  /* contact */
  .contact-label { color: var(--gold); font-size: 11.5px; letter-spacing: 2px; font-weight: 500; }
  .contact-row {
    left: 0; right: 0; display: flex; justify-content: center; align-items: center;
    color: var(--text-light); font-weight: 600;
  }
  .contact-item { display: flex; align-items: center; gap: 7px; }
  .contact-item svg { width: 14px; height: 14px; }
  .contact-item--phone { font-size: 14px; }
  .contact-item--mail, .contact-item--web { font-size: 11.8px; }
  .divider { width: 1px; height: 16px; background: var(--gold-deep); margin: 0 27px; }
  .brand { left: 0; right: 0; display: flex; justify-content: center; align-items: center; gap: 10px; }
  .brand-dot { width: 30px; height: 30px; border-radius: 50%; background: #cfc6ae; }
  .brand-name { color: #e8e4da; font-size: 31px; font-weight: 300; }

  /* back */
  .palace-photo {
    left: 0; top: 0; width: 740px; height: 660px;
    background:
      linear-gradient(to bottom, rgba(42,41,36,0) 86%, var(--ink-dark) 100%),
      linear-gradient(to bottom, var(--sky-top) 0%, #dcd6dc 25%, var(--sky-pink) 34%, #e7b9a4 40%, #d9d6d2 48%, #cfcac0 56%, #c8b75a 66%, #c8362a 78%, #c6b83c 88%, #4d5a2a 100%);
  }
  .sights { font-size: 16.5px; line-height: 28.5px; color: var(--text-dark); }
  .night-line { left: 67px; top: 220px; font-size: 16px; font-weight: 600; font-style: italic; color: var(--text-dark); }
  .others-panel { left: 78px; top: 622px; width: 597px; height: 289px; background: var(--panel); }
  .others-title { font-family: "Great Vibes", cursive; color: var(--gold); font-size: 50px; line-height: 1; }
  .others-list { color: var(--text-light); font-size: 13.5px; line-height: 28px; font-weight: 500; text-transform: uppercase; }
  .bespoke { font-size: 14.5px; line-height: 17px; }
</style>
</head>
<body>

<!-- FRONT -->
<section class="page page--front">
  <div class="abs castle-photo" role="img" aria-label="Photograph of Hollenby Castle at the end of a long tree-lined avenue under a pink sunset sky"></div>
  <h1 class="abs center script-title" style="top:28px;">Signature Tour</h1>
  <p class="abs center slogan" style="top:142px;">Amber Coachline..Ever at your service..</p>
  <p class="abs fleet-intro">We have a fleet of Valtrane E, S and V Class vehicles along with 16 Seater Executive Coaches so we can accommodate single travellers, couples, friends, families and groups.</p>

  <div class="abs tour-panel">
    <h2 class="abs tour-heading">VISIT TO THE HISTORIC<br>TOWN OF WINDSOR</h2>
    <div class="abs price-tag">
      <div class="amount"><sup>$</sup>8599<sup>.00</sup></div>
      <div class="note">(INCLUSIVE ALL TAXES)</div>
    </div>
    <div class="abs tour-stops">
      <p>Visiting the historic town of Windsor, Hollenby Castle, St Aldric’s Chapel and Regal Pemberly Shopping Arcade.</p>
      <p>Eton and Dunmere College with lovely view of the River Thames along with an array of Antique Shops in the quaint streets.</p>
      <p>Bray Village along with a visit to Heron Isle renowned for it’s Brevard Star Restaurants and pubs.</p>
      <p>Through picturesque Cookham along to Marlow for some shopping in the boutique shops, small listed buildings and beautiful places for refreshments, along with stunning views of the River Thames form Ashcombe Bridge.</p>
    </div>
    <p class="abs center quote" style="top:270px;"><span class="mark">“</span> Our signature tour is approximately 4 hours <span class="mark">”</span></p>
  </div>

  <p class="abs center contact-label" style="top:913px;">CONTACT US</p>
  <div class="abs contact-row" style="top:935px;">
    <span class="contact-item contact-item--phone">
      <svg viewBox="0 0 16 16" fill="none" stroke="#d2b94e" stroke-width="1.2"><circle cx="8" cy="8" r="7"/><path d="M5.5 4.5l1.3 1.5-.8 1.1c.6 1.2 1.4 2 2.6 2.6l1.1-.8 1.5 1.3-.8 1.2c-2.8-.4-5.2-2.8-5.6-5.6z"/></svg>
      01632 960417</span>
    <span class="divider"></span>
    <span class="contact-item contact-item--mail">
      <svg viewBox="0 0 16 16" fill="none" stroke="#d2b94e" stroke-width="1.2"><circle cx="8" cy="8" r="7"/><rect x="4.5" y="5.5" width="7" height="5"/><path d="M4.5 5.5l3.5 3 3.5-3"/></svg>
      sales@ambercoachline.co.uk</span>
    <span class="divider"></span>
    <span class="contact-item contact-item--web">
      <svg viewBox="0 0 16 16" fill="none" stroke="#d2b94e" stroke-width="1.2"><circle cx="8" cy="8" r="7"/><ellipse cx="8" cy="8" rx="3" ry="7"/><path d="M1 8h14"/></svg>
      www.ambercoachline.co.uk</span>
  </div>
  <div class="abs brand" style="top:985px;"><span class="brand-dot"></span><span class="brand-name">Amber Coachline</span></div>
</section>

<!-- BACK -->
<section class="page page--back">
  <div class="abs palace-photo" role="img" aria-label="Photograph of Corringdale Palace with its memorial statue and beds of red and yellow tulips in front"></div>
  <h1 class="abs center script-title" style="top:24px; color:#2a2620;">London Tours</h1>
  <ul class="abs sights" style="left:67px; top:114px; list-style:none;"><li>Belvards</li><li>Larkmoor Park</li><li>Ravensholt Palace</li></ul>
  <ul class="abs sights" style="left:267px; top:114px; list-style:none;"><li>Corringdale Palace</li><li>Pellington Square</li><li>Turning of the Sentries</li></ul>
  <ul class="abs sights" style="left:517px; top:110px; list-style:none;"><li>Keep of Ardmoor</li><li>Tall Tom</li><li>Glenmoreton Abbey</li></ul>
  <p class="abs night-line">Or maybe London by night with a show or restaurant.</p>

  <div class="abs others-panel">
    <h2 class="abs center others-title" style="top:16px;">Other Tours Provided</h2>
    <ul class="abs others-list" style="left:58px; top:94px; list-style:none;"><li>Ridgewell Court Palace</li><li>Oxford and Corvane Palace</li><li>Ashmarrow Ring and Bath</li></ul>
    <ul class="abs others-list" style="left:332px; top:88px; list-style:none;"><li>The Cotswolds</li><li>Stratford and Penlow Castle</li><li>Quillford Shopping Village</li></ul>
    <p class="abs center quote bespoke" style="top:200px;"><span class="mark">“</span> Also bespoke tours can be arranged. We can personalize any tour to <span class="mark">”</span><br>your requirements with our friendly, experienced chauffeurs</p>
  </div>

  <p class="abs center contact-label" style="top:933px;">CONTACT US</p>
  <div class="abs contact-row" style="top:954px;">
    <span class="contact-item contact-item--phone">
      <svg viewBox="0 0 16 16" fill="none" stroke="#d2b94e" stroke-width="1.2"><circle cx="8" cy="8" r="7"/><path d="M5.5 4.5l1.3 1.5-.8 1.1c.6 1.2 1.4 2 2.6 2.6l1.1-.8 1.5 1.3-.8 1.2c-2.8-.4-5.2-2.8-5.6-5.6z"/></svg>
      01632 960417</span>
    <span class="divider"></span>
    <span class="contact-item contact-item--mail">
      <svg viewBox="0 0 16 16" fill="none" stroke="#d2b94e" stroke-width="1.2"><circle cx="8" cy="8" r="7"/><rect x="4.5" y="5.5" width="7" height="5"/><path d="M4.5 5.5l3.5 3 3.5-3"/></svg>
      sales@ambercoachline.co.uk</span>
    <span class="divider"></span>
    <span class="contact-item contact-item--web">
      <svg viewBox="0 0 16 16" fill="none" stroke="#d2b94e" stroke-width="1.2"><circle cx="8" cy="8" r="7"/><ellipse cx="8" cy="8" rx="3" ry="7"/><path d="M1 8h14"/></svg>
      www.ambercoachline.co.uk</span>
  </div>
  <div class="abs brand" style="top:988px;"><span class="brand-dot"></span><span class="brand-name">Amber Coachline</span></div>
</section>

</body>
</html>
```